Corvana Tongue Works, LLC

We need a business card that includes information about our business and conveys a reliable business that provides document translation services and interpreters for a variety of corporate and individual clients. We want to come across as professional, reliable, yet approachable. It should include the following on one side:

ESL / ENL Language Classes, Private Lessons, and Online Tutors
PLEXA Training and Testing
Translating & Interpreting Services
Contact us about Over-the-Phone Interpreting in over 200 languages
24/7/365
www.corvanatongue.example

The other side should include (555) 481-3062

Rhoda Pelling, President
482 Garnet Ave., Ste. 219
Indianapolis, IN 40917

Please add USA as part of the address. Also, please add rmpelling@corvanatongueworks.example as the e-mail address. Thank you.

Target Market(s)

Business professionals, their families, the international community

Industry/Entity Type

Business

Contact Information for Business Card

24/7/365
www.corvanatongue.example

(555) 481-3062

Rhoda Pelling, President
482 Garnet Ave., Ste. 219
Indianapolis, IN 40917
USA

Font styles to use
Sans Serif

Colors

Designer to choose colors to be used in the design.

Requirements
Must have
• See project description
• e-mail address and web address
• Phone number
Nice to have
• a globe
• physical address
Should not have
• Should not have the same color scheme as other agencies in our market in Indiana unless it is blue and black. No purple or yellow.

```html
<!DOCTYPE html>
<html lang="en">
<head>
<meta charset="utf-8">
<title>Corvana Tongue Works, LLC – Business Card</title>
<link rel="stylesheet" href="https://fonts.googleapis.com/css2?family=Arimo:wght@400;500&display=swap">
<style>
  :root {
    --brand-blue: #2596d6;
    --ink: #111111;
    --paper: #ffffff;
    --mist: #eef3fa;
    --backdrop: #e4e6e9;
  }
  * { box-sizing: border-box; margin: 0; padding: 0; }
  html, body {
    width: 1189px; height: 1200px; overflow: hidden;
    background: var(--backdrop);
    font-family: "Arimo", Arial, sans-serif;
  }
  .card {
    position: absolute; left: 166px; width: 856px; height: 489px; overflow: hidden;
  }
  .card-front {
    top: 67px; background: var(--brand-blue);
    border-radius: 49px 0 49px 0;
  }
  .card-back {
    top: 626px; background: var(--paper);
    border-radius: 0 49px 0 49px;
  }
  .world-map {
    position: absolute; left: 70px; top: 40px; width: 716px; height: 330px;
    border-radius: 40%;
    background: radial-gradient(ellipse at center, rgba(20,110,170,0.22), rgba(20,110,170,0) 70%);
  }
  .brand-mark { position: absolute; }
  .brand-name {
    position: absolute; font-weight: 400; color: var(--ink); line-height: 1;
    white-space: nowrap;
  }
  .brand-name .line { display: block; }
  .brand-name .llc { font-size: 0.45em; }
  .front-mark { left: 254px; top: 73px; }
  .front-name { left: 410px; top: 85px; font-size: 43px; }
  .front-name .line { height: 45px; }
  .services {
    position: absolute; left: 0; width: 100%; top: 258px; text-align: center;
    color: var(--paper); font-size: 21px; line-height: 26.6px;
  }
  .web {
    position: absolute; font-size: 19px; letter-spacing: 4px; color: var(--ink);
  }
  .front-web { left: 0; width: 100%; top: 420px; text-align: center; }
  .back-ring { position: absolute; left: 0; top: 0; }
  .side-band { position: absolute; left: 0; top: 0; width: 110px; height: 100%; background: var(--brand-blue); }
  .side-rule { position: absolute; left: 113px; top: 0; width: 7px; height: 100%; background: var(--brand-blue); }
  .back-mark { left: 52px; top: 40px; }
  .back-name { left: 213px; top: 58px; font-size: 41px; }
  .back-name .line { height: 46px; }
  .contact {
    position: absolute; left: 215px; top: 244px; font-size: 20px; line-height: 25px; color: var(--ink);
  }
  .phone, .email {
    position: absolute; left: 215px; font-size: 20px; line-height: 25px; color: var(--ink);
  }
  .phone { top: 355px; }
  .email { top: 382px; }
  .phone b, .email b { color: var(--brand-blue); font-weight: 500; margin-right: 4px; }
  .back-web { left: 217px; top: 430px; }
  .back-web .domain { color: var(--brand-blue); }
</style>
</head>
<body>
  <section class="card card-front">
    <div class="world-map" role="img" aria-label="Faint world map behind the brand name"></div>
    <svg class="brand-mark front-mark" width="146" height="146" viewBox="0 0 146 146" aria-hidden="true">
      <circle cx="73" cy="73" r="71" fill="var(--paper)"/>
    </svg>
    <div class="brand-name front-name">
      <span class="line">Corvana</span><span class="line">Tongue</span><span class="line">Works <span class="llc">LLC</span></span>
    </div>
    <div class="services">
      ESL / ENL Language Classes, Private Lessons, and Online Tutors<br>
      PLEXA Training and Testing<br>
      Translating &amp; Interpreting Services<br>
      Contact us about Over-the-Phone Interpreting in over 200 languages<br>
      24/7/365
    </div>
    <div class="web front-web">www.corvanatongue.example</div>
  </section>

  <section class="card card-back">
    <svg class="back-ring" width="856" height="489" viewBox="0 0 856 489" aria-hidden="true">
      <circle cx="678" cy="206" r="248" fill="var(--mist)"/>
      <circle cx="678" cy="206" r="228" fill="none" stroke="var(--paper)" stroke-width="5"/>
    </svg>
    <div class="side-band"></div>
    <div class="side-rule"></div>
    <svg class="brand-mark back-mark" width="158" height="158" viewBox="0 0 158 158" aria-hidden="true">
      <circle cx="79" cy="79" r="75" fill="var(--brand-blue)" stroke="var(--paper)" stroke-width="6"/>
    </svg>
    <div class="brand-name back-name">
      <span class="line">Corvana</span><span class="line">Tongue</span><span class="line">Works <span class="llc">LLC</span></span>
    </div>
    <div class="contact">
      Rhoda Pelling, President<br>
      482 Garnet Ave., Ste. 219<br>
      Indianapolis, IN 40917<br>
      USA
    </div>
    <div class="phone"><b>P:</b>(555) 481-3062</div>
    <div class="email"><b>E:</b>rmpelling@corvanatongueworks.example</div>
    <div class="web back-web">www.<span class="domain">corvanatongue</span>.example</div>
  </section>
</body>
</html>
```